Bright Harbor Counseling Letterhead for hip modern business

I would like some ombre use of the colors in the logo hip letterhead that incorporates logo colors and feel, needs to connect with young professionals and college students. i need to be able to write letters to schools to excuse absences as well. i like color blocks on one side preferably using colors from the attached logo design.

Target Market(s)

high income young people, young adults and college students

Industry/Entity Type

mental health

Font styles to use
Serif
Sans Serif

Colors
0054AA
0677BA
7BADD7
CADEEF
E8F1F8
0094D4
00A9DD
6FCCEA
C7EBF8
E9F6FB
00AB8E
00BBA5
67D7C9
C6EFE9
E9F9F6
59FF00
82FF00
B8FF75
E3FFCB
F4FFEA
A7469A
B969AE
D3A5CF
EDDBEB
F8F0F9
6B429C
8869AF
B7A5CE
E3DAEB
F3F0F8

Requirements
Must have
• a modern hip feel, somewhat color

```html
<!DOCTYPE html>
<html lang="en">
<head>
<meta charset="utf-8">
<title>Bright Harbor Counseling – Letterhead</title>
<link rel="stylesheet" href="https://fonts.googleapis.com/css2?family=Mulish:wght@300;400;500&display=swap">
<style>
  :root {
    --backdrop: #2e2e2e;
    --paper: #ffffff;
    --ink: #2b2b2b;
    --ink-soft: #444444;
    --teal: #5cc8bd;
    --magenta: #b969ae;
    --sky: #5aa6d8;
    --indigo: #4f4aa3;
    --violet: #8869af;
    --mist: #e9f1f8;
  }
  * { box-sizing: border-box; margin: 0; padding: 0; }
  html, body {
    width: 1200px;
    height: 941px;
    overflow: hidden;
    background: var(--backdrop);
    font-family: "Mulish", "Helvetica Neue", Arial, sans-serif;
  }
  .canvas {
    position: relative;
    width: 1200px;
    height: 941px;
  }
  .letterhead {
    position: absolute;
    left: 289px;
    top: 30px;
    width: 622px;
    height: 880px;
    background: var(--paper);
    box-shadow: 0 6px 24px rgba(0, 0, 0, 0.45);
    overflow: hidden;
  }
  .brand {
    position: absolute;
    left: 48px;
    top: 58px;
    display: flex;
    align-items: center;
    gap: 10px;
  }
  .brand-dot {
    width: 18px;
    height: 18px;
    border-radius: 50%;
    background: var(--magenta);
  }
  .brand-name {
    font-size: 21px;
    font-weight: 300;
    letter-spacing: 0.4px;
    color: var(--ink);
  }
  .backdrop-mark {
    position: absolute;
    left: 236px;
    top: 330px;
    width: 150px;
    height: 150px;
    border-radius: 50%;
    background: radial-gradient(circle at 40% 40%, #eef0fa 0%, #f4eef7 60%, rgba(255,255,255,0) 100%);
  }
  .contact {
    position: absolute;
    right: 34px;
    bottom: 38px;
    text-align: right;
    font-size: 11px;
    line-height: 17px;
    color: var(--ink-soft);
  }
  .contact-name {
    color: var(--magenta);
    font-weight: 400;
  }
  .contact-row {
    display: flex;
    justify-content: flex-end;
    align-items: center;
    gap: 5px;
    white-space: nowrap;
  }
  .contact-icon {
    width: 11px;
    height: 11px;
    flex: none;
  }
  .color-band {
    position: absolute;
    left: 0;
    right: 0;
    bottom: 0;
    height: 12px;
    display: flex;
  }
  .color-band span { flex: 1; }
  .band-teal { background: var(--teal); }
  .band-magenta { background: var(--magenta); }
  .band-sky { background: var(--sky); }
  .band-indigo { background: var(--indigo); }
</style>
</head>
<body>
<main class="canvas">
  <article class="letterhead">
    <header class="brand">
      <span class="brand-dot"></span>
      <span class="brand-name">Bright Harbor Counseling</span>
    </header>

    <div class="backdrop-mark" aria-hidden="true"></div>

    <footer class="contact">
      <p class="contact-name">Bright Harbor Counseling</p>
      <p>Suite 210 Harbor Lane, State, Zip 4120, Country</p>
      <p class="contact-row">
        <svg class="contact-icon" viewBox="0 0 12 12" aria-hidden="true"><circle cx="6" cy="6" r="6" fill="#5cc8bd"/><path d="M4 3.2l1 .2.4 1.3-.7.6a4 4 0 0 0 1.9 1.9l.6-.7 1.3.4.2 1a4.8 4.8 0 0 1-4.7-4.7z" fill="#fff"/></svg>
        <span>(00) 01234 555 210</span>
        <svg class="contact-icon" viewBox="0 0 12 12" aria-hidden="true"><circle cx="6" cy="6" r="6" fill="#b969ae"/><rect x="3.5" y="3" width="5" height="6" rx="0.6" fill="none" stroke="#fff" stroke-width="1"/></svg>
        <span>(00) 01234 555 211</span>
        <svg class="contact-icon" viewBox="0 0 12 12" aria-hidden="true"><circle cx="6" cy="6" r="6" fill="#5aa6d8"/><rect x="3" y="4" width="6" height="4" fill="none" stroke="#fff" stroke-width="0.9"/><path d="M3 4l3 2.2L9 4" fill="none" stroke="#fff" stroke-width="0.9"/></svg>
        <span>hello@brightharbor.com</span>
        <svg class="contact-icon" viewBox="0 0 12 12" aria-hidden="true"><circle cx="6" cy="6" r="6" fill="#4f4aa3"/><circle cx="6" cy="6" r="3" fill="none" stroke="#fff" stroke-width="0.9"/><path d="M3 6h6M6 3v6" stroke="#fff" stroke-width="0.7"/></svg>
        <span>www.brightharborcounseling.com</span>
      </p>
    </footer>

    <div class="color-band" aria-hidden="true">
      <span class="band-teal"></span>
      <span class="band-magenta"></span>
      <span class="band-sky"></span>
      <span class="band-indigo"></span>
    </div>
  </article>
</main>
</body>
</html>
```